Design and Renovation Company Luxury Business Card

I want to create a luxury business card for a Design and Renovation Firm . We will use our current logo. The company name is 528BUILDA. We do not want anything standard. We need a very unique concept.
Please see uploaded inspiration. I really like the textured paper option. I would like the card to be thick with debossing, and/or embossing options. The logo has orange in it but I would like to see the card with and without the orange. I think the orange may make the company feel less high-end. The goal is to elevate the logo not match its vibe per se of the logo. We want something very unique, not standard at all!
I would like a space for :
Logo,
Name,
Position,
Email,
Office number,
Website Address,
Business Address,
Thank you!
Have fun!
Target Market(s)
Home owners Age 35 +
Industry/Entity Type
Design and Renovation
Contact Information for Business Card
Logo, Name, Position, Email, Office number, Website Address, Business Address,.
Colors
Designer to choose colors to be used in the design.
Requirements
Must have
- A luxury designer feel. Must be black or dark grey but open to other luxury ideas.
Nice to have
- Gold, silver, black embossing or debossing. Textured paper design.
Should not have
- A cheap look and feel.

```html
<!DOCTYPE html>
<html lang="en">
<head>
<meta charset="utf-8">
<title>528BUILDA Business Card</title>
<link href="https://fonts.googleapis.com/css2?family=Montserrat:wght@400;500;700&display=swap" rel="stylesheet">
<style>
  :root {
    --backdrop: #9a9a9a;
    --card-white: #ffffff;
    --card-black: #161616;
    --ink: #111111;
    --accent: #f39322;
    --paper-white: #ffffff;
    --tile-dark: #050505;
    --tile-light: #5a5a5a;
  }
  * { box-sizing: border-box; margin: 0; padding: 0; }
  html, body {
    width: 1093px; height: 1200px; overflow: hidden;
    background: var(--backdrop);
    font-family: "Montserrat", sans-serif;
    color: var(--ink);
  }
  .canvas { position: relative; width: 1093px; height: 1200px; }
  .card {
    position: absolute; left: 264px; width: 597px; height: 364px;
    border-radius: 18px; overflow: hidden;
  }
  .card-front { top: 225px; background: var(--card-white); border: 1px solid #7c7c7c; }
  .card-back { top: 616px; background: var(--card-black); }

  .brand-name { position: absolute; font-weight: 700; letter-spacing: 0; line-height: 1; white-space: nowrap; }
  .front-brand { left: 20px; top: 34px; font-size: 33px; color: var(--ink); }

  .person { position: absolute; right: 30px; top: 24px; text-align: right; }
  .person-name { font-size: 23px; font-weight: 700; line-height: 1.1; }
  .person-title { font-size: 14px; font-weight: 400; margin-top: 4px; }

  .contact-list { position: absolute; left: 27px; top: 272px; list-style: none; }
  .contact-list li { display: flex; align-items: center; gap: 7px; font-size: 14px; height: 23.5px; }
  .contact-list svg { width: 14px; height: 14px; flex: none; }

  .address { position: absolute; left: 389px; top: 306px; font-size: 14px; line-height: 17px; font-style: normal; }

  .tile-field {
    position: absolute; inset: 0;
    background: linear-gradient(100deg, var(--tile-dark) 0%, #121212 35%, #2e2e2e 70%, var(--tile-light) 100%);
  }
  .back-brand { right: 71px; top: 236px; font-size: 42px; color: var(--paper-white); }
</style>
</head>
<body>
<main class="canvas">
  <section class="card card-front" aria-label="Business card front">
    <p class="brand-name front-brand">528BUILDA</p>

    <div class="person">
      <p class="person-name">Daniel Marlow</p>
      <p class="person-title">Managing Director</p>
    </div>

    <ul class="contact-list">
      <li>
        <svg viewBox="0 0 16 16" aria-hidden="true"><path fill="var(--accent)" d="M3.6 1.5 6 4.2 4.7 5.9c.8 1.9 2.3 3.4 4.2 4.3l1.6-1.4 2.7 2.4-1.4 2.6C6.5 13.6 2.3 9.4 1.1 3.1z"/></svg>
        <span>555-014-0128</span>
      </li>
      <li>
        <svg viewBox="0 0 16 16" aria-hidden="true"><rect x="1" y="3.5" width="14" height="9" rx="1" fill="var(--accent)"/><path d="M1.5 4.2 8 8.8l6.5-4.6" fill="none" stroke="#fff" stroke-width="1.2"/></svg>
        <span>info@yourstudiosite.com</span>
      </li>
      <li>
        <svg viewBox="0 0 16 16" aria-hidden="true"><circle cx="8" cy="8" r="6.5" fill="none" stroke="var(--accent)" stroke-width="1.6"/><ellipse cx="8" cy="8" rx="2.6" ry="6.5" fill="none" stroke="var(--accent)" stroke-width="1.3"/><path d="M1.5 8h13" stroke="var(--accent)" stroke-width="1.3"/></svg>
        <span>www.yourstudiosite.com</span>
      </li>
    </ul>

    <address class="address">418 Alder Court, #112<br>Brookhaven, OH 43015</address>
  </section>

  <section class="card card-back" aria-label="Business card back">
    <div class="tile-field" role="img" aria-label="Grid of square tiles fading from black on the left to grey on the right"></div>
    <p class="brand-name back-brand">528BUILDA</p>
  </section>
</main>
</body>
</html>
```